Simple and clean

We need a business card design for a new company called Dwelling Hawk. It is a search engine to find current properties for sale or rent in New Zealand market.
We have already a colour scheme that we would like people to use.
Light brown: #D4CCB0
Light green: #D6E4D4
Green: #669966
Black/White
It is OK to divert from this colour scheme slightly as long as there is a green component to the business card.
Final design should be clean, simple and should communicate the nature of the business.
Target Market(s)
- First home buyers
- Real estate agents
- People seeking rentals
Industry/Entity Type
Business
Requirements
Must have
- Use those or similar colours.
Light brown: #D4CCB0
Light green: #D6E4D4
Green: #669966
Black/White

```html
<!DOCTYPE html>
<html lang="en">
<head>
<meta charset="utf-8">
<title>Dwelling Hawk – Business Card</title>
<link rel="stylesheet" href="https://fonts.googleapis.com/css2?family=Source+Sans+3:ital,wght@0,400;0,700;1,400&display=swap">
<style>
  :root {
    --card-black: #000000;
    --brand-green: #58bf43;
    --text-white: #ffffff;
    --web-grey: #b5b5b5;
    --frame-grey: #9a9a9a;
    --dot-grey: #d9d9d9;
  }
  html, body {
    margin: 0;
    padding: 0;
    width: 1200px;
    height: 702px;
    overflow: hidden;
    background: #ffffff;
  }
  .card {
    position: relative;
    width: 1200px;
    height: 702px;
    box-sizing: border-box;
    border: 2px solid var(--frame-grey);
    background: var(--card-black);
    overflow: hidden;
    font-family: "Source Sans 3", sans-serif;
  }
  .card__swoosh {
    position: absolute;
    inset: 0;
  }
  .brand__dot {
    position: absolute;
    left: 60px;
    top: 58px;
    width: 158px;
    height: 158px;
    border-radius: 50%;
    background: var(--dot-grey);
  }
  .brand__name {
    position: absolute;
    left: 238px;
    top: 50px;
    margin: 0;
    color: var(--brand-green);
    font-size: 80px;
    font-weight: 400;
    line-height: 1;
    letter-spacing: -0.5px;
    white-space: nowrap;
  }
  .contact > * {
    position: absolute;
    right: 70px;
    margin: 0;
    color: var(--text-white);
    line-height: 1;
    text-align: right;
    white-space: nowrap;
  }
  .contact__name {
    top: 214px;
    font-size: 40px;
    font-weight: 700;
  }
  .contact__role {
    top: 260px;
    font-size: 34px;
    font-style: italic;
  }
  .contact__mobile {
    top: 350px;
    font-size: 34px;
  }
  .contact__email {
    top: 394px;
    font-size: 34px;
  }
  .website {
    position: absolute;
    left: 66px;
    top: 586px;
    margin: 0;
    color: var(--web-grey);
    font-size: 55px;
    line-height: 1;
    white-space: nowrap;
  }
</style>
</head>
<body>
  <div class="card">
    <svg class="card__swoosh" width="1200" height="702" viewBox="0 0 1200 702" aria-hidden="true">
      <path d="M1200 0 L1190 0 C 820 40, 598 170, 598 343 C 598 510, 860 650, 1200 692 Z" fill="var(--brand-green)"/>
    </svg>

    <div class="brand__dot" aria-hidden="true"></div>
    <h1 class="brand__name">DwellingHawk</h1>

    <div class="contact">
      <p class="contact__name">Liam Carter</p>
      <p class="contact__role">Director</p>
      <p class="contact__mobile">Mobile: 04x-xxx-xxxx</p>
      <p class="contact__email">Email: l.carter@dwellinghawk.co.nz</p>
    </div>

    <p class="website">www.dwellinghawk.co.nz</p>
  </div>
</body>
</html>
```